Heron Haulage needs Bussiness cards!

Our new trucking company needs business cards!
We need the same design with two different names and emails, everything else it's the same.
I have included our original logo so we can use it for the design.
Note: the logo to be used is the o e with the buffalo on the right side, next to the letters H and H.

Target Market(s)

Trucking, refrigerated transportation, freight

Industry/Entity Type

Business

Contact Information for Business Card

Card #1:
Marcus Whitfield
marcuswhitfield@heronhaulage.example
1-855-317-6094
(956)238-7160
4117 W. Larkin Ave.
Pharr, TX 78590
www.heronhaulage.example

Card#2:
Rosalba Quintero
rosalba@heronhaulage.example
1-855-317-6094
(956)238-7160
4117 W. Larkin Ave.
Pharr, TX 78590
www.heronhaulage.example

Font styles to use
Sans Serif

Colors
0655a3
ec1f27
ffffff

Requirements
Must have
• our logo
Nice to have
• roads on background,

```html
<!DOCTYPE html>
<html lang="en">
<head>
<meta charset="utf-8">
<title>Heron Haulage — Business Cards</title>
<link href="https://fonts.googleapis.com/css2?family=Roboto:wght@300;400;900&display=swap" rel="stylesheet">
<style>
  :root {
    --brand-blue: #0655a3;
    --brand-navy: #17335f;
    --brand-red: #ec1f27;
    --paper: #ffffff;
    --ink: #4a4a4a;
    --backdrop: #e9eaec;
  }
  * { margin: 0; padding: 0; box-sizing: border-box; }
  html, body { width: 1200px; height: 810px; overflow: hidden; }
  body {
    background: var(--backdrop);
    font-family: "Roboto", Arial, sans-serif;
    position: relative;
  }
  .card {
    position: absolute;
    width: 520px;
    height: 298px;
    background: var(--paper);
    border-radius: 18px;
    overflow: hidden;
    box-shadow: 0 6px 18px rgba(0,0,0,.18);
  }
  .card--front { left: 50px; top: 256px; }
  .card--back { left: 630px; top: 256px; }

  .wordmark {
    position: absolute;
    display: flex;
    align-items: center;
    gap: 8px;
    color: var(--brand-navy);
    font-weight: 900;
    font-size: 30px;
    line-height: 1;
    letter-spacing: -0.5px;
    white-space: nowrap;
  }
  .wordmark__dot {
    width: 22px; height: 22px;
    border-radius: 50%;
    background: var(--brand-red);
    flex: none;
  }
  .card--front .wordmark { left: 150px; top: 120px; }
  .card--back .wordmark { left: 32px; top: 112px; font-size: 26px; }

  .front__web {
    position: absolute;
    left: 0; right: 0; top: 206px;
    text-align: center;
    color: var(--brand-blue);
    font-size: 12px;
    font-weight: 400;
  }

  .holder {
    position: absolute;
    right: 30px; top: 28px;
    color: var(--brand-red);
    font-size: 20px;
    font-weight: 400;
    letter-spacing: .3px;
  }
  .contact {
    position: absolute;
    right: 30px; top: 68px;
    text-align: right;
    color: var(--ink);
    font-size: 11.5px;
    font-weight: 300;
    line-height: 1.45;
  }
  .contact__address { margin-bottom: 10px; }
  .contact__line { display: flex; justify-content: flex-end; align-items: center; gap: 6px; }
  .contact__line svg { width: 11px; height: 11px; fill: var(--brand-blue); flex: none; }
  .contact__email { margin-top: 8px; }

  .swoosh { position: absolute; inset: 0; width: 100%; height: 100%; }
  .back__web {
    position: absolute;
    left: 28px; top: 272px;
    color: var(--paper);
    font-size: 12px;
    font-weight: 400;
    transform: rotate(-2deg);
    transform-origin: left center;
    white-space: nowrap;
  }
</style>
</head>
<body>

  <section class="card card--front" aria-label="Business card front">
    <div class="wordmark"><span class="wordmark__dot"></span>Heron Haulage</div>
    <p class="front__web">www.heronhaulage.example</p>
  </section>

  <section class="card card--back" aria-label="Business card back">
    <svg class="swoosh" viewBox="0 0 520 298" preserveAspectRatio="none" aria-hidden="true">
      <path d="M0,236 C180,240 340,226 520,206 L520,216 C340,236 180,250 0,246 Z" fill="var(--brand-red)"/>
      <path d="M0,252 C180,256 340,242 520,222 L520,226 C340,246 180,260 0,256 Z" fill="var(--brand-blue)"/>
      <path d="M0,262 C180,266 340,252 520,232 L520,298 L0,298 Z" fill="var(--brand-blue)"/>
    </svg>

    <div class="wordmark"><span class="wordmark__dot"></span>Heron Haulage</div>

    <h1 class="holder">Marcus Whitfield</h1>

    <div class="contact">
      <p class="contact__address">4117 W. Larkin Ave. Pharr<br>TX 78590</p>
      <p class="contact__line">1-855-317-6094
        <svg viewBox="0 0 24 24" aria-hidden="true"><path d="M6.6 10.8a15 15 0 0 0 6.6 6.6l2.2-2.2a1 1 0 0 1 1-.25 11.4 11.4 0 0 0 3.6.57 1 1 0 0 1 1 1V20a1 1 0 0 1-1 1A17 17 0 0 1 3 4a1 1 0 0 1 1-1h3.5a1 1 0 0 1 1 1c0 1.25.2 2.45.57 3.57a1 1 0 0 1-.25 1z"/></svg>
      </p>
      <p class="contact__line">(956)238-7160
        <svg viewBox="0 0 24 24" aria-hidden="true"><path d="M7 1h10a2 2 0 0 1 2 2v18a2 2 0 0 1-2 2H7a2 2 0 0 1-2-2V3a2 2 0 0 1 2-2zm0 3v14h10V4zm5 15.5a1 1 0 1 0 0 2 1 1 0 0 0 0-2z"/></svg>
      </p>
      <p class="contact__line contact__email">marcuswhitfield@heronhaulage.example
        <svg viewBox="0 0 24 24" aria-hidden="true"><path d="M2 5h20v14H2zm2 2v.5l8 5 8-5V7zm0 2.8V17h16V9.8l-8 5z"/></svg>
      </p>
    </div>

    <p class="back__web">www.heronhaulage.example</p>
  </section>

</body>
</html>
```